Valdane Companies Business Card Design

We need a new business card for our Private Equity Real Estate Development firm, “Valdane” and our EB-5 regional center “Thornmere Regional Center” on one card. We prefer a design that is simple, elegant, and represents the luxury products we design and build as well as the financial security and stability our successful history has produced. We are an industry leader in our field and 3rd generation family business that has evolved into an institutional quality investment platform. Considered design size is standard business card dimensions (3.5 x 2 inches with an additional 1/8 inch space for design elements or backgrounds that extend beyond the finished size of your piece.

Target Market(s)

• High net worth individuals
• Highly skilled technical workers and physicians in the US seeking investment-based immigration opportunities
• Sophisticated private equity investors
• Intermediary partners include domestic attorneys and investment brokers, as well as international agent networks
• US real estate developers

Industry/Entity Type

Finance

Contact Information for Business Card

(Providing placeholder info for personal information, please design for longer character spaces, longer names and addresses etc..)
• Logo for Valdane
• Logo for Thornmere Regional Center
• Full name: Marcus Valdane
• Job title: CEO
• Email address: mvaldane@valdanecompanies.com
• Cell phone number: +1.555.314.2287
• Office number +1.555.628.4410
• Office address: Larkfield Court 5, 4817 Vista Orilla, Ashcombe Vale.
• Website: www.valdanecompanies.com

Font styles to use
Serif
Sans Serif

Colors
ec1f27
ffffff
000000

Requirements
Must have
• • Logo for Valdane
• • Logo for Thornmere Regional Center
• - Use rounded corners
• (See .ai file included for logos)
Nice to have
• • Simple, elegant design
• • Aesthetically compatible with our website design (www.valdanecompanies.com)
• • Color palette including but not limited to white, black, and red (as per logos)
Should not have
• - Not too much red color
• - Do not stack both logos on top of each other

```html
<!DOCTYPE html>
<html lang="en">
<head>
<meta charset="utf-8">
<title>Valdane Companies Business Card</title>
<link href="https://fonts.googleapis.com/css2?family=Cinzel:wght@400;600&family=Source+Sans+3:wght@300;400;600&display=swap" rel="stylesheet">
<style>
  :root {
    --backdrop: #8a8a8a;
    --card-white: #ffffff;
    --card-grey: #dcdbdc;
    --ink: #2a2a2a;
    --ink-soft: #3a3a3a;
    --accent-red: #a51c30;
    --rule: #b9b8b9;
    --back-dark: #2e2e2e;
    --back-pattern: #383838;
    --back-text: #d2d2d2;
  }
  * { margin: 0; padding: 0; box-sizing: border-box; }
  html, body { width: 1200px; height: 1200px; overflow: hidden; }
  body { background: var(--backdrop); position: relative; font-family: "Source Sans 3", Arial, sans-serif; }

  .card {
    position: absolute; top: 311px; width: 364px; height: 593px;
    border-radius: 6px; overflow: hidden;
    box-shadow: 2px 3px 6px rgba(0,0,0,.35);
  }
  .card--front { left: 234px; background: var(--card-white); }
  .card--back  { left: 628px; width: 368px; background: var(--back-dark); }

  .front-shapes { position: absolute; inset: 0; }

  .brand {
    position: absolute; top: 48px; left: 0; width: 100%;
    text-align: center; color: var(--ink);
  }
  .brand__mark { width: 84px; height: 84px; margin: 0 auto 24px; background: var(--ink); border-radius: 4px; }
  .brand__name { font-family: "Cinzel", Georgia, serif; font-weight: 600; font-size: 52px; line-height: 1; letter-spacing: 1px; }
  .brand__sub { font-size: 16px; font-weight: 400; letter-spacing: 9px; margin-top: 8px; padding-left: 9px; }

  .contact { position: absolute; top: 344px; left: 0; width: 100%; text-align: center; color: var(--ink-soft); }
  .contact__name { font-family: "Cinzel", Georgia, serif; font-weight: 600; font-size: 24px; color: var(--accent-red); letter-spacing: .3px; }
  .contact__title { font-size: 16px; margin-top: 0; }
  .contact__rule { width: 226px; height: 1px; background: var(--rule); margin: 6px auto 10px; }
  .contact__lines { font-size: 16.5px; line-height: 21.5px; }
  .contact__lines b { font-weight: 600; }
  .contact__web { color: var(--accent-red); }
  .contact__address { font-size: 16.5px; line-height: 21.5px; margin-top: 17px; }

  .back-pattern { position: absolute; inset: 0; width: 100%; height: 100%; }
  .center-brand {
    position: absolute; left: 34px; top: 482px;
    display: flex; align-items: center; gap: 12px; color: var(--back-text);
  }
  .center-brand__mark { width: 58px; height: 58px; background: var(--back-text); border-radius: 4px; }
  .center-brand__divider { width: 1px; height: 62px; background: var(--back-text); }
  .center-brand__name { font-family: "Cinzel", Georgia, serif; font-weight: 600; font-size: 30px; line-height: 1; }
  .center-brand__sub { font-size: 12px; font-weight: 400; letter-spacing: 4.5px; margin-top: 6px; }
</style>
</head>
<body>
  <section class="card card--front">
    <svg class="front-shapes" viewBox="0 0 364 593" width="364" height="593">
      <polygon points="0,329 364,249 364,593 0,593" fill="var(--card-grey)"/>
      <polygon points="0,296 354,250 0,329" fill="var(--accent-red)"/>
    </svg>
    <div class="brand">
      <div class="brand__mark"></div>
      <div class="brand__name">VALDANE</div>
      <div class="brand__sub">CAPITAL</div>
    </div>
    <div class="contact">
      <div class="contact__name">MARCUS VALDANE</div>
      <div class="contact__title">CEO</div>
      <div class="contact__rule"></div>
      <div class="contact__lines">
        <div><b>P:</b> +1.555.314.2287</div>
        <div><b>M:</b> +1.555.628.4410</div>
        <div><b>E:</b> mvaldane@valdanecompanies.com</div>
        <div><b>W:</b> www.<span class="contact__web">valdanecompanies</span>.com</div>
      </div>
      <div class="contact__address">Larkfield Court 5, 4817 Vista<br>Orilla, Ashcombe Vale</div>
    </div>
  </section>

  <section class="card card--back">
    <svg class="back-pattern" viewBox="0 0 368 593" role="img" aria-label="Faint repeating brand-symbol pattern">
      <rect width="368" height="593" fill="var(--back-pattern)" opacity=".35"/>
    </svg>
    <div class="center-brand">
      <div class="center-brand__mark"></div>
      <div class="center-brand__divider"></div>
      <div>
        <div class="center-brand__name">THORNMERE</div>
        <div class="center-brand__sub">REGIONAL CENTER</div>
      </div>
    </div>
  </section>
</body>
</html>
```